Lumora Systems New Website - IT Infrastructure | Smart Cabinet | Micro Data Center

We're an IT SI providing Server Room Design & Build | All-in-One Rack & Smart Cabinet | Structured Cabling | IT Relocation | Maintenance. Old website can be found at www.lumorasys.com.hk. We'd like a brand new wix website which is modern, minimalist, interactive with some animation. Website content will be mostly static and include our service, our project, news and events, about us, contacts, blogs, partners and brands, etc.

reference sites:
We'd like to see more designs referring to below

https://www.pixelvane.example/design/41736205
https://www.pixelvane.example/design/41892417
https://velbrinn.example/

Animation (scrolling effect) referring to
https://velbrinn.example/intelligence/smart-office-room/
Updates

we'd like below style.

Designs look the same

Target Market(s)

Commercials in HK

Industry/Entity Type

IT, Technology, Data Center

Coding

Coded - Design and coding required

Font styles to use
Sans Serif

Requirements
Must have
• CMS, Some Interactive Elements/ Graphics

```html
<!DOCTYPE html>
<html lang="en">
<head>
<meta charset="utf-8">
<title>Lumora Systems – IT Infrastructure | Smart Cabinet | Micro Data Center</title>
<link href="https://fonts.googleapis.com/css2?family=Barlow:wght@300;400;500&family=Montserrat:wght@400;500;600;700&display=swap" rel="stylesheet">
<style>
:root{
  --navy:#111b3f;
  --navy-deep:#0b1434;
  --red:#d93a22;
  --orange:#e2611f;
  --white:#ffffff;
  --ink:#2b2b2b;
  --muted:#555a66;
  --line:#c9ccd3;
  --photo-blue:#1d4f8f;
  --photo-dark:#101a2e;
}
*{box-sizing:border-box;margin:0;padding:0}
html,body{width:1200px;height:4910px;overflow:hidden}
body{position:relative;background:var(--white);font-family:"Montserrat",sans-serif;color:var(--ink)}
.abs{position:absolute}
.heading{font-family:"Barlow",sans-serif;font-weight:400;font-size:38px;color:var(--ink);text-align:center;width:100%;position:absolute;left:0}
.heading.light{color:var(--white)}
.heading .bar{display:block;width:70px;height:3px;background:var(--red);margin:6px auto 0}
.btn{position:absolute;background:var(--red);color:var(--white);font-size:14px;font-weight:500;border-radius:8px;display:flex;align-items:center;justify-content:center;letter-spacing:.3px}
.photo{position:absolute;background:linear-gradient(160deg,#2f6bb0,var(--photo-dark))}
.photo.warm{background:linear-gradient(160deg,#8a6a58,#1a2236)}
.photo.dark{background:linear-gradient(160deg,#3a3f4a,#0c0f16)}
.readmore{font-size:13px;font-weight:600;text-decoration:underline;letter-spacing:.3px}

/* header + hero */
.hero{position:absolute;left:0;top:0;width:1200px;height:620px}
.hero-photo{position:absolute;left:0;top:0;width:1200px;height:580px;background:linear-gradient(180deg,#0d1f45 0%,#14427e 45%,#1c5fa8 70%,#0e2a5c 100%)}
.topbar{position:absolute;left:0;top:0;width:1200px;height:90px;background:rgba(12,20,52,.92)}
.brand{position:absolute;left:130px;top:26px;display:flex;align-items:center;gap:10px;color:var(--white);font-family:"Montserrat",sans-serif;font-weight:500;font-size:26px}
.brand .mark{width:26px;height:26px;border:3px solid var(--white)}
.nav{position:absolute;right:114px;top:28px;display:flex;gap:26px;align-items:center;font-size:15px;color:var(--white);font-weight:500}
.nav .cta{background:var(--red);border-radius:8px;padding:9px 16px}
.hero-title{position:absolute;left:0;top:238px;width:1200px;text-align:center;font-family:"Barlow",sans-serif;font-size:42px;color:var(--white);font-weight:400}
.scroll-badge{position:absolute;left:564px;top:566px;width:72px;height:72px;border-radius:50%;background:var(--white);border:5px solid #c6c8cc;display:flex;align-items:center;justify-content:center}

/* services */
.service{position:absolute;top:770px;width:227px;height:263px;overflow:hidden;box-shadow:0 3px 10px rgba(0,0,0,.18)}
.service .photo{left:0;top:0;width:100%;height:198px}
.service .label{position:absolute;left:0;bottom:0;width:100%;height:65px;background:var(--navy);color:var(--white);font-size:15px;font-weight:500;text-align:center;display:flex;align-items:center;justify-content:center;line-height:1.6}
.service .label.active{background:var(--red)}

/* about */
.about{position:absolute;left:0;top:1118px;width:1200px;height:560px;background:var(--navy)}
.about h2{position:absolute;left:602px;top:80px;font-family:"Barlow",sans-serif;font-weight:400;font-size:38px;color:var(--white)}
.about p{position:absolute;left:602px;top:150px;width:492px;font-size:14.5px;line-height:25.7px;color:#e6e8f0}

/* projects */
.projects-intro{position:absolute;left:150px;top:1845px;width:900px;text-align:center;font-size:14.5px;line-height:26px;color:var(--muted)}
.project{position:absolute;top:1934px;width:286px;height:207px}
.project.overlay{background:var(--red);color:var(--white);display:flex;flex-direction:column;align-items:center;justify-content:center;text-align:center;font-size:16px;font-weight:600;line-height:1.6}
.dots{position:absolute;left:566px;top:2162px;display:flex;gap:4px}
.dots span{width:14px;height:14px;border-radius:50%;border:2px solid var(--ink)}
.dots span.on{background:var(--ink)}

/* news */
.news{position:absolute;left:0;top:2263px;width:1200px;height:657px;background:linear-gradient(100deg,var(--orange),var(--red))}
.feature{position:absolute;left:118px;top:158px;width:490px;height:414px;background:var(--navy-deep)}
.feature .photo{left:0;top:0;width:490px;height:277px}
.feature .txt{position:absolute;left:18px;top:296px;width:450px;color:var(--white)}
.feature h3{font-size:16px;font-weight:500;line-height:26px}
.feature small{display:block;font-size:12.5px;margin:8px 0 6px}
.item{position:absolute;left:659px;width:470px;height:126px}
.item .photo{left:0;top:0;width:168px;height:126px}
.item .txt{position:absolute;left:189px;top:0;width:270px;color:var(--white);font-size:16px;line-height:26px}
.item .readmore{display:block;margin-top:18px}

/* partners */
.partner{position:absolute;width:170px;height:44px;border-radius:6px;background:#d9dbe0}

/* contact */
.contact{position:absolute;left:0;top:3374px;width:1200px;height:634px;background:var(--navy)}
.contact h3{position:absolute;left:110px;top:160px;font-size:29px;font-weight:600;color:var(--white)}
.info{position:absolute;left:110px;font-size:15.5px;color:var(--white);line-height:25px}
.info b{position:absolute;left:0;font-weight:700}
.info span{position:absolute;left:96px;width:320px}
.map{position:absolute;left:110px;top:360px;width:427px;height:188px;border-radius:22px;background:linear-gradient(135deg,#4a4d55,#2c2f36)}
.form{position:absolute;left:631px;top:154px;width:459px;height:394px;background:var(--white);border-radius:14px}
.form h4{position:absolute;left:26px;top:20px;font-size:29px;font-weight:600;color:var(--navy)}
.field{position:absolute;width:191px;height:34px;border:1.5px solid var(--line);border-radius:6px;font-size:13.5px;color:#333;padding:8px 14px}
.field.msg{width:404px;height:71px}

/* blogs */
.blog{position:absolute;top:4162px;width:265px;height:349px;background:var(--white);box-shadow:0 3px 12px rgba(0,0,0,.15)}
.blog .photo{left:0;top:0;width:265px;height:191px}
.blog .body{position:absolute;left:16px;top:204px;width:232px;font-size:14.5px;line-height:26px;color:var(--muted)}
.blog .date{color:var(--red);display:flex;align-items:center;gap:6px}
.blog .readmore{color:var(--red);display:block;margin-top:6px}
.arrow{position:absolute;top:4320px;width:38px;height:38px;border-radius:50%;border:2.5px solid var(--ink);display:flex;align-items:center;justify-content:center}

/* footer */
.footer{position:absolute;left:0;top:4599px;width:1200px;height:311px;background:var(--navy)}
.footer .brand{left:110px;top:92px}
.footer .about-txt{position:absolute;left:110px;top:150px;width:340px;font-size:14.5px;line-height:26px;color:var(--white)}
.footer h5{position:absolute;top:86px;font-family:"Barlow",sans-serif;font-weight:400;font-size:21px;color:var(--white)}
.footer ul{position:absolute;top:126px;list-style:none;font-size:14.5px;line-height:26px;color:var(--white)}
.footer .copy{position:absolute;left:867px;top:158px;width:240px;font-size:14.5px;line-height:26px;color:var(--white)}
.social{position:absolute;top:225px;width:22px;height:22px;border-radius:50%;background:var(--white)}
</style>
</head>
<body>

<!-- Header and hero -->
<section class="hero">
  <div class="hero-photo" role="img" aria-label="Rows of illuminated server racks in a blue-lit data center"></div>
  <svg class="abs" style="left:0;top:0" width="1200" height="620" viewBox="0 0 1200 620">
    <polygon points="0,446 600,548 1200,446 1200,620 0,620" fill="#ffffff"/>
    <polygon points="0,436 600,538 1200,436 1200,452 600,566 0,452" fill="#d93a22"/>
  </svg>
  <div class="topbar"></div>
  <div class="brand"><span class="mark"></span>Lumora Systems</div>
  <nav class="nav"><span>HOME</span><span>ABOUT</span><span>OUR SERVICES</span><span>OUR PROJECTS</span><span class="cta">CONTACT US</span></nav>
  <h1 class="hero-title">IT Infrastructure | Smart Cabinet | Micro Data Center</h1>
  <div class="btn" style="left:538px;top:331px;width:126px;height:36px">GET STARTED</div>
  <div class="scroll-badge">
    <svg width="22" height="36" viewBox="0 0 22 36"><rect x="2" y="2" width="18" height="26" rx="9" fill="none" stroke="#2b2b2b" stroke-width="2"/><line x1="11" y1="7" x2="11" y2="12" stroke="#2b2b2b" stroke-width="2"/><path d="M7 31l4 4 4-4" fill="none" stroke="#2b2b2b" stroke-width="1.6"/></svg>
  </div>
</section>

<!-- Services -->
<h2 class="heading" style="top:692px">Our Services</h2>
<article class="service" style="left:110px"><div class="photo" role="img" aria-label="Engineers reviewing a server rack"></div><div class="label active">Data Center Design &amp;<br>Build</div></article>
<article class="service" style="left:362px"><div class="photo" role="img" aria-label="Structured network cabling close-up"></div><div class="label">Structured Cabling &amp;<br>Fiber Backbone</div></article>
<article class="service" style="left:613px"><div class="photo dark" role="img" aria-label="Technician working on an all-in-one rack"></div><div class="label">All - In- One Race<br>/ Micro - Data Center</div></article>
<article class="service" style="left:863px"><div class="photo" role="img" aria-label="Server room with conference equipment"></div><div class="label">Audiovisual &amp;<br>Conference Room</div></article>

<!-- About -->
<section class="about">
  <svg class="abs" style="left:490px;top:57px" width="76" height="36"><g fill="#8f97b4"><circle cx="3" cy="3" r="1.6"/><circle cx="13" cy="3" r="1.6"/><circle cx="23" cy="3" r="1.6"/><circle cx="33" cy="3" r="1.6"/><circle cx="43" cy="3" r="1.6"/><circle cx="53" cy="3" r="1.6"/><circle cx="63" cy="3" r="1.6"/><circle cx="73" cy="3" r="1.6"/><circle cx="3" cy="13" r="1.6"/><circle cx="13" cy="13" r="1.6"/><circle cx="23" cy="13" r="1.6"/><circle cx="33" cy="13" r="1.6"/><circle cx="43" cy="13" r="1.6"/><circle cx="53" cy="13" r="1.6"/><circle cx="63" cy="13" r="1.6"/><circle cx="73" cy="13" r="1.6"/><circle cx="3" cy="23" r="1.6"/><circle cx="13" cy="23" r="1.6"/><circle cx="23" cy="23" r="1.6"/><circle cx="33" cy="23" r="1.6"/><circle cx="43" cy="23" r="1.6"/><circle cx="53" cy="23" r="1.6"/><circle cx="63" cy="23" r="1.6"/><circle cx="73" cy="23" r="1.6"/><circle cx="3" cy="33" r="1.6"/><circle cx="13" cy="33" r="1.6"/><circle cx="23" cy="33" r="1.6"/><circle cx="33" cy="33" r="1.6"/><circle cx="43" cy="33" r="1.6"/><circle cx="53" cy="33" r="1.6"/><circle cx="63" cy="33" r="1.6"/><circle cx="73" cy="33" r="1.6"/></g></svg>
  <div class="photo warm" style="left:225px;top:86px;width:299px;height:248px" role="img" aria-label="IT professional in front of server racks"></div>
  <div class="photo dark" style="left:114px;top:244px;width:223px;height:231px" role="img" aria-label="Engineer with laptop in a server aisle"></div>
  <div class="photo" style="left:362px;top:351px;width:189px;height:124px" role="img" aria-label="Overhead view of a data hall"></div>
  <h2>About Us</h2>
  <p>Lumora Systems is well experienced in delivering the best in Data Center Infrastructure, Network Infrastructure, Structured Cabling, Telephony, Access Control, Video Surveillance, Audiovisual &amp; Conferencing, Relocation &amp; Migration and Maintenance solutions.<br>Our dedication, focus, and expertise wins much recognition of many IT professionals in all industries in the region. In Lumora Systems's Belief, the major reason that we gain a lot of true long-lasting business relationship with our clients was that we offer them the attention, consideration</p>
  <div class="btn" style="left:602px;top:437px;width:126px;height:36px">READ MORE</div>
</section>

<!-- Projects -->
<h2 class="heading" style="top:1754px">Our Projects</h2>
<p class="projects-intro">With our vendor-independent expertise in best-of-breed IT infrastucture solution, not only are we to fulfill your business needs with unbiased recommendation, but we also help IT Professionals create the most cost-effective</p>
<div class="project photo dark" style="left:110px" role="img" aria-label="Black smart cabinets installed in a server room"></div>
<div class="project photo" style="left:457px" role="img" aria-label="Bundled blue network cables in a rack"></div>
<div class="project overlay" style="left:802px"><span>A renowned china based<br>securities firm</span><span class="readmore" style="margin-top:14px">READ MORE</span></div>
<div class="dots"><span></span><span></span><span class="on"></span><span></span></div>

<!-- News -->
<section class="news">
  <h2 class="heading light" style="top:80px">News &amp; Events<span class="bar" style="background:var(--navy)"></span></h2>
  <article class="feature">
    <div class="photo dark" role="img" aria-label="Developer working at multiple monitors"></div>
    <div class="txt"><h3>Lorem ipsum dolor sit amet, consectetur adipiscing elit, sed do eiusmod tempor</h3><small>Lorem ipsum dolor sit amet, consectetur adipiscing elit,</small><span class="readmore">READ MORE</span></div>
  </article>
  <article class="item" style="top:158px"><div class="photo" role="img" aria-label="Technician at a server rack"></div><div class="txt">Lorem ipsum dolor sit amet, consectetur<span class="readmore">READ MORE</span></div></article>
  <article class="item" style="top:303px"><div class="photo" role="img" aria-label="Engineers walking in a data center aisle"></div><div class="txt">Lorem ipsum dolor sit amet, consectetur<span class="readmore">READ MORE</span></div></article>
  <article class="item" style="top:448px"><div class="photo" role="img" aria-label="Team inspecting network equipment"></div><div class="txt">Lorem ipsum dolor sit amet, consectetur<span class="readmore">READ MORE</span></div></article>
</section>

<!-- Partners -->
<h2 class="heading" style="top:2986px">Our Partners</h2>
<div class="partner" style="left:117px;top:3072px"></div>
<div class="partner" style="left:315px;top:3072px"></div>
<div class="partner" style="left:513px;top:3072px"></div>
<div class="partner" style="left:713px;top:3072px"></div>
<div class="partner" style="left:913px;top:3072px"></div>
<div class="partner" style="left:117px;top:3150px"></div>
<div class="partner" style="left:315px;top:3150px"></div>
<div class="partner" style="left:513px;top:3150px"></div>
<div class="partner" style="left:713px;top:3150px"></div>
<div class="partner" style="left:913px;top:3150px"></div>
<div class="partner" style="left:117px;top:3228px"></div>
<div class="partner" style="left:315px;top:3228px"></div>
<div class="partner" style="left:513px;top:3228px"></div>
<div class="partner" style="left:713px;top:3228px"></div>

<!-- Contact -->
<section class="contact">
  <h2 class="heading light" style="top:78px">Contact Us<span class="bar"></span></h2>
  <h3>Mailing Information</h3>
  <div class="info" style="top:228px"><b>Address</b><span>Rm 908, 9/F, Harbour Crest Centre, 18 Kinwell Road</span></div>
  <div class="info" style="top:280px"><b>Phone</b><span>+852 2000 4812 / +852 5000 7391</span></div>
  <div class="info" style="top:315px"><b>Email</b><span>marketing@lumorasys.com.hk</span></div>
  <div class="map" role="img" aria-label="Street map showing the office location"></div>
  <form class="form">
    <h4>Get In Touch</h4>
    <div class="field" style="left:26px;top:97px">First Name</div>
    <div class="field" style="left:240px;top:97px">Last Name</div>
    <div class="field" style="left:26px;top:151px">Phone</div>
    <div class="field" style="left:240px;top:151px">Email</div>
    <div class="field" style="left:26px;top:204px">Location</div>
    <div class="field" style="left:240px;top:204px">Subject</div>
    <div class="field msg" style="left:26px;top:238px">Message</div>
    <div class="btn" style="left:26px;top:335px;width:128px;height:37px">SUBMIT</div>
  </form>
</section>

<!-- Blogs -->
<h2 class="heading" style="top:4085px">Our Blogs</h2>
<div class="arrow" style="left:111px"><svg width="14" height="14"><path d="M9 2L4 7l5 5" fill="none" stroke="#2b2b2b" stroke-width="2"/></svg></div>
<div class="arrow" style="left:1050px"><svg width="14" height="14"><path d="M5 2l5 5-5 5" fill="none" stroke="#2b2b2b" stroke-width="2"/></svg></div>
<article class="blog" style="left:170px"><div class="photo warm" role="img" aria-label="Colleagues with a laptop in a server room"></div><div class="body"><span class="date"><svg width="13" height="13"><circle cx="6.5" cy="6.5" r="5.5" fill="none" stroke="#d93a22" stroke-width="1.5"/><path d="M6.5 3.5v3h2.5" fill="none" stroke="#d93a22" stroke-width="1.5"/></svg>Dec 09, 2023</span>Lorem ipsum dolor sit amet, consectetur adipiscing elit, sed do eiusmod<span class="readmore">READ MORE</span></div></article>
<article class="blog" style="left:469px"><div class="photo" role="img" aria-label="Abstract digital network graphic"></div><div class="body"><span class="date"><svg width="13" height="13"><circle cx="6.5" cy="6.5" r="5.5" fill="none" stroke="#d93a22" stroke-width="1.5"/><path d="M6.5 3.5v3h2.5" fill="none" stroke="#d93a22" stroke-width="1.5"/></svg>Dec 09, 2023</span>Lorem ipsum dolor sit amet, consectetur adipiscing elit, sed do eiusmod<span class="readmore">READ MORE</span></div></article>
<article class="blog" style="left:766px"><div class="photo dark" role="img" aria-label="Rack-mounted server hardware"></div><div class="body"><span class="date"><svg width="13" height="13"><circle cx="6.5" cy="6.5" r="5.5" fill="none" stroke="#d93a22" stroke-width="1.5"/><path d="M6.5 3.5v3h2.5" fill="none" stroke="#d93a22" stroke-width="1.5"/></svg>Dec 09, 2023</span>Lorem ipsum dolor sit amet, consectetur adipiscing elit, sed do eiusmod<span class="readmore">READ MORE</span></div></article>

<!-- Footer -->
<footer class="footer">
  <div class="brand"><span class="mark"></span>Lumora Systems</div>
  <p class="about-txt">Our dedication, focus, and expertise wins much recognition of many IT professionals in all industries in the region.</p>
  <h5 style="left:503px">Company</h5>
  <ul style="left:503px"><li>Home</li><li>About</li><li>Services</li><li>Project</li><li>Partner</li><li>Blog</li></ul>
  <h5 style="left:655px">Other Links</h5>
  <ul style="left:655px"><li>Faqs</li><li>Terms &amp; Condition</li><li>Privacy Policy</li><li>Cookie Policy</li></ul>
  <div class="btn" style="left:867px;top:87px;width:150px;height:36px">CONTACT</div>
  <p class="copy">© 2023 Lumora Systems. All Rights Reserved.</p>
  <span class="social" style="left:864px"></span>
  <span class="social" style="left:904px"></span>
</footer>

</body>
</html>
```